2021 Summer Ads Hollis Bay Custom Homes

We need a re-design of our summer ad run for our customer, Hollis Bay Custom Homes. They are custom home builders in the mostly rural parts of West Virginia, USA. They are known for their "Forever Home" tagline. We'd like two designed ads with the main difference being just the custom home that's featured. These designs should be for a Zintrola banner like 300 x 250 and square ad like 250 x 250. For inspiration please visit the Hollis Bay Custom Homes website at www dot hollisbaycustomhomes dot com

Target Market(s)

consumers / new home shoppers

Industry/Entity Type

Consumer

Requirements
Must have
• HBCH logo
Price Lock Available!
Custom home pic
Learn more >
small CFRM logo mark

```html
<!DOCTYPE html>
<html lang="en">
<head>
<meta charset="utf-8">
<title>Hollis Bay Custom Homes – Start Building Your Forever Home Today</title>
<link rel="stylesheet" href="https://fonts.googleapis.com/css2?family=Poppins:wght@500;600;700&display=swap">
<style>
  :root {
    --brand-red: #e31b2d;
    --brand-red-dark: #b5101f;
    --ink-navy: #1d2230;
    --paper: #ffffff;
    --badge-blue: #1f4aa8;
    --sky-top: #3f86d4;
    --sky-mid: #a9cde9;
    --house-white: #eef0f2;
    --lawn-green: #4d7a34;
  }
  html, body {
    margin: 0;
    padding: 0;
    width: 1200px;
    height: 1000px;
    overflow: hidden;
    background: var(--paper);
  }
  .ad-canvas {
    position: relative;
    width: 1200px;
    height: 1000px;
    overflow: hidden;
    background: var(--paper);
    font-family: "Poppins", Arial, sans-serif;
  }
  .ad-shapes {
    position: absolute;
    inset: 0;
    width: 1200px;
    height: 1000px;
  }
  .headline {
    position: absolute;
    left: 84px;
    top: 82px;
    margin: 0;
    font-size: 62px;
    line-height: 88px;
    font-weight: 600;
    color: var(--ink-navy);
    letter-spacing: -0.5px;
  }
  .headline .accent { color: var(--brand-red); }
  .headline span { display: block; }
  .price-lock {
    position: absolute;
    left: 88px;
    top: 432px;
    margin: 0;
    font-size: 30px;
    font-weight: 600;
    color: var(--brand-red);
    letter-spacing: 0.5px;
  }
  .cta-button {
    position: absolute;
    left: 86px;
    top: 506px;
    width: 326px;
    height: 92px;
    border-radius: 10px;
    background: var(--brand-red);
    color: var(--paper);
    text-decoration: none;
    display: flex;
    align-items: center;
    box-sizing: border-box;
    padding-left: 40px;
    font-size: 27px;
    font-weight: 600;
    letter-spacing: 0.5px;
  }
  .cta-arrow {
    position: absolute;
    right: 14px;
    top: 16px;
    width: 60px;
    height: 60px;
  }
  .builder-name {
    position: absolute;
    left: 60px;
    top: 660px;
    display: flex;
    align-items: center;
    gap: 18px;
    font-size: 34px;
    line-height: 42px;
    font-weight: 700;
    color: var(--brand-red);
  }
  .builder-name .mark {
    width: 44px;
    height: 44px;
    background: var(--brand-red);
    flex: none;
  }
  .partner-badge {
    position: absolute;
    left: 62px;
    top: 838px;
    width: 200px;
    height: 128px;
    border-radius: 8px;
    background: var(--badge-blue);
  }
</style>
</head>
<body>
<main class="ad-canvas">
  <svg class="ad-shapes" viewBox="0 0 1200 1000" aria-hidden="false">
    <defs>
      <linearGradient id="home-photo-tone" x1="0" y1="0" x2="0" y2="1">
        <stop offset="0" stop-color="var(--sky-top)"/>
        <stop offset="0.35" stop-color="var(--sky-mid)"/>
        <stop offset="0.55" stop-color="var(--house-white)"/>
        <stop offset="0.8" stop-color="#9a9a94"/>
        <stop offset="1" stop-color="var(--lawn-green)"/>
      </linearGradient>
    </defs>
    <polygon class="corner-tint" points="0,0 120,0 0,110" fill="var(--brand-red)" opacity="0.12"/>
    <polygon class="diagonal-band" points="660,0 862,0 330,1000 292,1000" fill="var(--brand-red)"/>
    <polygon class="home-photo" role="img" aria-label="Photo of a white board-and-batten custom home with stone base, black carriage garage doors and landscaped garden under a blue sky"
             points="886,0 1200,0 1200,1000 352,1000" fill="url(#home-photo-tone)"/>
  </svg>

  <h1 class="headline">
    <span class="accent">Start</span>
    <span class="accent">Building</span>
    <span>Your Forever</span>
    <span>Home Today!</span>
  </h1>

  <p class="price-lock">PRICE LOCK AVAILABLE!</p>

  <a class="cta-button" href="#">
    LEARN MORE
    <svg class="cta-arrow" viewBox="0 0 60 60" aria-hidden="true">
      <circle cx="30" cy="30" r="30" fill="var(--brand-red-dark)"/>
      <polyline points="25,18 37,30 25,42" fill="none" stroke="#ffffff" stroke-width="5" stroke-linecap="round" stroke-linejoin="round"/>
    </svg>
  </a>

  <div class="builder-name">
    <span class="mark"></span>
    <span>Hollis Bay<br>Custom Homes</span>
  </div>

  <div class="partner-badge" role="img" aria-label="CFRM member badge"></div>
</main>
</body>
</html>
```